Harborview Estates Business Card for Apartment Buildings

Create business cards for resident managers who run apartment buildings. The audience is the public who are searching for apartment rentals, and current residents who live at the apartment building. Key design element will be incorporating the company logo, however, the logo cannot dominate. The building name and manager name are more important than the logo. Current business card design leaves little room for copy, so we may need to reduce the size on the current card to allow for more space for copy.

Target Market(s)

Adults 18-65 years of age, who are looking for an apartment rental, plus current residents who live at our apartment buildings.

Industry/Entity Type

Property Management

Contact Information for Business Card

A major design element will be use of the company logo. Important property and manager contact information must be part of the design. The size of the logo will need to be reduced to make room for building and manager contact copy.

Font styles to use
Sans Serif

Colors
3176b5
000000
959595
ffffff

Requirements
Must have
• 1) Incorporate the company logo.
• 2) Use the company colors (dark blue, black/grey, over white).
• 3) FEATURE THE BUILDING NAME
• 4) FEATURE THE MANAGER NAME
• 5) The company name is less important than BUILDING and MANAGER
• 6) Manager contact information
• **SEE ATTACHED CREATIVE BRIEF**
Nice to have
• 1) Back of card logo watermark
• 2) Ability to write notes on back of carfd
Should not have
• Avoid letting the company logo dominate the card, the building name and manager are more important than the company logo.

```html
<!DOCTYPE html>
<html lang="en">
<head>
<meta charset="utf-8">
<title>Harborview Estates Business Card</title>
<link href="https://fonts.googleapis.com/css2?family=Montserrat:wght@400;500;700;800&family=Oswald:wght@500&display=swap" rel="stylesheet">
<style>
  :root {
    --brand-blue: #3176b5;
    --ink: #2b2c30;
    --card-dark: #4a4b4f;
    --band-grey: #58595d;
    --muted: #959595;
    --white: #ffffff;
    --backdrop: #e9e9ea;
  }
  * { margin: 0; padding: 0; box-sizing: border-box; }
  html, body { width: 1200px; height: 930px; overflow: hidden; }
  body {
    background: var(--backdrop);
    font-family: "Montserrat", sans-serif;
    position: relative;
  }
  .card {
    position: absolute;
    width: 580px;
    height: 331px;
    border-radius: 16px;
    overflow: hidden;
    box-shadow: 0 6px 18px rgba(0,0,0,.18);
  }

  /* Back of card */
  .card-back { left: 90px; top: 80px; background: var(--card-dark); }
  .card-back .wordmark {
    position: absolute; left: 0; right: 0; top: 105px;
    display: flex; align-items: center; justify-content: center; gap: 16px;
    color: var(--white); font-weight: 800;
  }
  .card-back .wordmark .dot {
    width: 34px; height: 34px; border-radius: 50%; background: var(--white); flex: none;
  }
  .card-back .wordmark .name { font-size: 40px; line-height: 1; letter-spacing: .5px; }
  .card-back .wordmark .sub {
    display: block; font-size: 16px; letter-spacing: 5px; margin-top: 6px;
  }
  .card-back .site {
    position: absolute; left: 0; right: 0; top: 246px; text-align: center;
    color: var(--white); font-size: 13px; letter-spacing: .5px;
  }

  /* Front of card */
  .card-front { left: 530px; top: 510px; background: var(--white); }
  .card-front .band {
    position: absolute; left: 0; top: 66px; width: 118px; height: 56px;
    background: var(--band-grey);
  }
  .card-front .wordmark {
    position: absolute; left: 88px; top: 48px;
    display: flex; align-items: center; gap: 12px;
    color: var(--brand-blue); font-weight: 800; line-height: 1;
  }
  .card-front .wordmark .square {
    width: 26px; height: 26px; background: var(--brand-blue); flex: none;
  }
  .card-front .wordmark .name { font-size: 28px; letter-spacing: .3px; }
  .card-front .wordmark .sub {
    display: block; font-size: 11px; letter-spacing: 3px; margin-top: 5px;
  }
  .manager {
    position: absolute; right: 30px; top: 82px; text-align: right;
  }
  .manager .name {
    font-family: "Oswald", sans-serif; font-weight: 500; font-size: 30px;
    color: var(--brand-blue); letter-spacing: .3px; line-height: 1;
    text-transform: uppercase;
  }
  .manager .role { font-size: 12.5px; color: #444; margin-top: 4px; }
  .divider {
    position: absolute; left: 170px; right: 150px; top: 140px;
    height: 1.5px; background: var(--brand-blue);
  }
  .address {
    position: absolute; right: 30px; top: 160px; text-align: right;
    font-size: 12.5px; line-height: 20px; color: #333;
  }
  .address .building {
    display: block; font-size: 14px; font-weight: 700; color: var(--ink);
  }
  .contacts {
    position: absolute; left: 170px; top: 200px; list-style: none;
    font-size: 13px; line-height: 21px; color: #333;
  }
  .contacts li { display: flex; align-items: center; gap: 10px; }
  .contacts svg { width: 11px; height: 11px; fill: var(--brand-blue); flex: none; }
  .contacts .accent { color: var(--brand-blue); }
</style>
</head>
<body>

<section class="card card-back" aria-label="Card back">
  <div class="wordmark">
    <i class="dot"></i>
    <span><span class="name">HARBORVIEW</span><span class="sub">ESTATES LLC</span></span>
  </div>
  <p class="site">www.harborviewest.com</p>
</section>

<section class="card card-front" aria-label="Card front">
  <div class="band"></div>
  <div class="wordmark">
    <i class="square"></i>
    <span><span class="name">HARBORVIEW</span><span class="sub">ESTATES LLC</span></span>
  </div>

  <div class="manager">
    <p class="name">Marisol Vega</p>
    <p class="role">Resident Manager</p>
  </div>
  <div class="divider"></div>

  <p class="address"><span class="building">Cedar Court Apartments</span>1482 Linden Avenue<br>Fairview, CA 94027</p>

  <ul class="contacts">
    <li><svg viewBox="0 0 12 12"><path d="M3 1l2 2-1 1.5c.6 1.4 1.6 2.4 3 3L8.5 6.5l2 2-1.5 2C5 10 2 7 1.5 2.5z"/></svg><span>555-210-4410</span></li>
    <li><svg viewBox="0 0 12 12"><path d="M3.5 0h5a1 1 0 0 1 1 1v10a1 1 0 0 1-1 1h-5a1 1 0 0 1-1-1V1a1 1 0 0 1 1-1zm.5 1.5v7.5h4V1.5z"/></svg><span>555-318-7702</span></li>
    <li><svg viewBox="0 0 12 12"><rect x="1" y="4" width="10" height="6" rx="1"/><rect x="3" y="1" width="6" height="3"/></svg><span>555-406-2290</span></li>
    <li><svg viewBox="0 0 12 12"><path d="M0 2h12v8H0zm1 1v.4l5 3.2 5-3.2V3z"/></svg><span>marisol@harborviewest.com</span></li>
    <li><svg viewBox="0 0 12 12"><circle cx="6" cy="6" r="5.5"/></svg><span>www.<span class="accent">harborviewest.com</span></span></li>
  </ul>
</section>

</body>
</html>
```